New Business Card for Software Company

We are looking at rebranding a 10 year old company that specializes in PDF and DWF solutions for Architects and Engineers. We will attach the new company logo that we are going with so you can work with that and complimentary colors.
The sample information we would like on the business card is:
Gerald Pinfold
Vice President
4738 W. Harrowgate Lane. STE 305
PMB#417
Mesa, AZ 85374
866-392-5074 US Toll Free
123-456-3190 Cell
gpinfold@plavorix.com
The old tag line that we had on the business cars was.
Delivering Dependable Drawing and File Tools to Design Teams Around the World.
If you have an idea for a better tag line we are open to that also.
Updates
We would like to thank all of the Designers for their wonderful work. We apologize that we will not have the time to provide feedback to everyone. There is just so many innovative and professional designs that you have all created making our decision even harder.
Target Market(s)
Architects and Engineers
Industry/Entity Type
Business
Look and feel

```html
<!DOCTYPE html>
<html lang="en">
<head>
<meta charset="utf-8">
<title>Plavorix Business Card</title>
<link rel="stylesheet" href="https://fonts.googleapis.com/css2?family=Open+Sans:wght@400;700&display=swap">
<style>
  :root {
    --backdrop: #ece7e1;
    --card-white: #ffffff;
    --brand-orange: #f26522;
    --brand-red: #d9362b;
    --brand-amber: #f7941d;
    --wedge-grey: #5f6062;
    --text-grey: #4a4a4a;
    --divider: #c9c9c9;
    --tagline: #fde9c8;
  }
  * { margin: 0; padding: 0; box-sizing: border-box; }
  html, body {
    width: 1200px; height: 720px; overflow: hidden;
    background: var(--backdrop);
    font-family: "Open Sans", Arial, sans-serif;
  }
  .stage {
    position: relative; width: 1200px; height: 720px;
    display: flex; align-items: center; justify-content: center; gap: 40px;
  }
  .card {
    position: relative; width: 540px; height: 309px;
    border-radius: 3px; overflow: hidden;
    box-shadow: 0 6px 18px rgba(0,0,0,0.18);
  }
  /* Front */
  .card-front { background: var(--card-white); }
  .corner-art { position: absolute; inset: 0; }
  .holder { position: absolute; top: 8px; right: 18px; text-align: right; color: #fff; }
  .holder-name { font-weight: 700; font-size: 15px; line-height: 1.2; }
  .holder-title { font-size: 10px; line-height: 1.2; }
  .brand { position: absolute; left: 34px; top: 112px; display: flex; align-items: center; gap: 14px; }
  .brand-dot { width: 56px; height: 56px; border-radius: 50%; background: var(--brand-orange); }
  .brand-name { font-weight: 700; font-size: 50px; color: var(--brand-orange); letter-spacing: -1px; line-height: 1; }
  .contacts { position: absolute; left: 34px; top: 212px; list-style: none; }
  .contacts li {
    display: flex; align-items: center; gap: 8px;
    font-size: 12px; color: var(--text-grey); line-height: 22px;
  }
  .contacts svg { width: 11px; height: 11px; flex: none; }
  .divider { position: absolute; left: 262px; top: 186px; width: 1px; height: 52px; background: var(--divider); }
  .address { position: absolute; left: 276px; top: 184px; font-size: 12px; font-style: normal; color: var(--text-grey); line-height: 22px; }
  /* Back */
  .card-back {
    background: radial-gradient(ellipse at 50% 40%, var(--brand-amber) 0%, var(--brand-orange) 55%, var(--brand-red) 100%);
    display: flex; flex-direction: column; align-items: center;
  }
  .back-mark { margin-top: 40px; width: 104px; height: 104px; border-radius: 50%; background: #f9a94a; }
  .back-name { margin-top: 12px; font-weight: 700; font-size: 26px; color: #fff; line-height: 1; }
  .tagline { margin-top: 30px; text-align: center; font-size: 16px; line-height: 1.4; color: var(--tagline); }
</style>
</head>
<body>
<main class="stage">
  <section class="card card-front" aria-label="Business card front">
    <svg class="corner-art" viewBox="0 0 540 309" aria-hidden="true">
      <defs>
        <linearGradient id="bandFill" x1="0" y1="0" x2="1" y2="0">
          <stop offset="0" stop-color="#f7941d"/>
          <stop offset="1" stop-color="#d9362b"/>
        </linearGradient>
      </defs>
      <polygon points="230,0 540,0 540,52 318,44" fill="url(#bandFill)"/>
      <path d="M318,44 L540,52 L540,60 C520,78 505,100 498,128 Z" fill="var(--wedge-grey)"/>
    </svg>
    <div class="holder">
      <p class="holder-name">Gerald Pinfold</p>
      <p class="holder-title">Vice President</p>
    </div>
    <div class="brand">
      <span class="brand-dot"></span>
      <span class="brand-name">Plavorix</span>
    </div>
    <ul class="contacts">
      <li>
        <svg viewBox="0 0 12 12"><circle cx="6" cy="6" r="6" fill="var(--brand-orange)"/><path d="M4 3 L5.2 3 L5.6 4.6 L4.9 5.2 Q5.6 6.6 6.9 7.1 L7.5 6.4 L9 6.8 L9 8 Q5 8.5 4 3 Z" fill="#fff"/></svg>
        866-392-5074US(TF)
      </li>
      <li>
        <svg viewBox="0 0 12 12"><rect x="3" y="0.5" width="6" height="11" rx="1.2" fill="var(--brand-orange)"/><rect x="4" y="2" width="4" height="6" fill="#fff"/></svg>
        123-456-3190
      </li>
      <li>
        <svg viewBox="0 0 12 12"><circle cx="6" cy="6" r="6" fill="var(--brand-red)"/><rect x="2.8" y="3.8" width="6.4" height="4.4" fill="#fff"/><path d="M2.8 3.8 L6 6.4 L9.2 3.8" stroke="var(--brand-red)" stroke-width="0.8" fill="none"/></svg>
        gpinfold@plavorix.com
      </li>
    </ul>
    <span class="divider"></span>
    <address class="address">
      4738 W. Harrowgate Lane. STE 305<br>
      PMB#417, Mesa, AZ 85374
    </address>
  </section>

  <section class="card card-back" aria-label="Business card back">
    <span class="back-mark"></span>
    <p class="back-name">Plavorix</p>
    <p class="tagline">Delivering Dependable Drawing and File Tools<br>to Design Teams Around the World</p>
  </section>
</main>
</body>
</html>
```